Business card for Eyelash extension salon in Beverly Hills,California USA

We need new business card for our salon in Beverly Hills. The salon name is 'Lashvera' . We would like to have...Business name: Lashvera Name of person: will provide later Address 4720 N.Alder Crest Ave Beverly Hills , CA 90210 Phone: will provide later (Text only) Web: www.lashverastudio.example Snapgrid icon, Circlebook icon follow us for seasonal campaign and news @lashverastudiolounge Design should look elegant, high-end, clean, simple, cohesive with my brand. Please refer my brand board. Business name color will be metallic bronzy color. Im thinking grey background or white background. Thanks

Target Market(s)

25-35. Gender neutral. People who are in Entertainment business industry.
This is High-end Eyelash extension salon in Beverly Hills

Industry/Entity Type

Beauty Salon

Contact Information for Business Card

Business name: Lashvera
Name of person: will provide later
Address 4720 N.Alder Crest Ave Beverly Hills , CA 90210
Phone: will provide later (Text only)
Web: www.lashverastudio.example
Snapgrid icon, Circlebook icon
follow us for seasonal campaign and news @lashverastudiolounge

Requirements
Must have
• Beautiful, elegant, clean and simple look but very attractive and modern
Should not have
• We don't like too clutter, too busy designs.

```html
<!DOCTYPE html>
<html lang="en">
<head>
<meta charset="utf-8">
<title>Lashvera Business Card</title>
<link rel="stylesheet" href="https://fonts.googleapis.com/css2?family=Bodoni+Moda:wght@400;600;700&family=Raleway:wght@400;500&display=swap">
<style>
  :root {
    --backdrop: #2f2f30;
    --card-white: #f4f3f1;
    --bronze: #8a6a52;
    --ink: #4a4644;
    --muted-grey: #a9a6a3;
    --gold-dark: #c9a768;
    --gold-mid: #ddbd7f;
    --gold-light: #f6da9a;
    --white: #ffffff;
  }
  * { margin: 0; padding: 0; box-sizing: border-box; }
  html, body { width: 1200px; height: 960px; overflow: hidden; }
  body { background: var(--backdrop); position: relative; font-family: "Bodoni Moda", serif; }

  .card { position: absolute; width: 600px; height: 343px; overflow: hidden; box-shadow: 0 4px 14px rgba(0,0,0,.45); }

  /* Front */
  .card-front { left: 186px; top: 113px; background: var(--card-white); }
  .interior-photo {
    position: absolute; inset: 0;
    background:
      radial-gradient(ellipse at 55% 75%, rgba(150,140,132,.28), transparent 55%),
      linear-gradient(90deg, #ecebe9 0%, #f7f7f6 35%, #efeeec 70%, #e6e4e2 100%);
  }
  .brand-name-front {
    position: absolute; left: 40px; top: 52px;
    font-size: 60px; font-weight: 400; color: var(--bronze); letter-spacing: 1px; line-height: 1.2;
  }
  .brand-locale-front {
    position: absolute; left: 40px; width: 222px; top: 153px; text-align: right;
    font-family: "Raleway", sans-serif; font-size: 9px; letter-spacing: 1.6px; color: var(--bronze);
  }
  .person { position: absolute; left: 40px; top: 238px; }
  .person-name { font-size: 21px; font-weight: 700; color: var(--bronze); line-height: 1; letter-spacing: .3px; }
  .person-role { font-size: 14px; font-weight: 600; color: var(--muted-grey); line-height: 1.3; }
  .address {
    position: absolute; left: 352px; top: 194px; font-style: normal;
    font-size: 14px; line-height: 18px; color: var(--ink);
  }
  .contact-list { position: absolute; left: 352px; top: 259px; list-style: none; }
  .contact-list li { display: flex; align-items: center; gap: 8px; font-size: 13.5px; line-height: 19.5px; color: var(--ink); white-space: nowrap; }
  .contact-list svg { width: 13px; height: 13px; fill: var(--bronze); flex: none; }

  /* Back */
  .card-back {
    left: 434px; top: 511px;
    background: linear-gradient(90deg, var(--gold-dark) 0%, var(--gold-mid) 30%, var(--gold-light) 50%, var(--gold-mid) 72%, var(--gold-dark) 100%);
  }
  .social { position: absolute; right: 34px; top: 36px; display: flex; gap: 10px; }
  .social-item { display: flex; align-items: center; gap: 4px; font-size: 11px; color: var(--white); }
  .social-item .dot { width: 9px; height: 9px; border-radius: 50%; background: var(--white); }
  .brand-name-back {
    position: absolute; left: 0; right: 0; top: 104px; text-align: center;
    font-size: 80px; font-weight: 400; color: var(--white); letter-spacing: 1px; line-height: 1.2;
  }
  .brand-locale-back {
    position: absolute; left: 200px; width: 186px; top: 218px; text-align: right;
    font-family: "Raleway", sans-serif; font-size: 9px; letter-spacing: 1.6px; color: var(--white);
  }
  .web-back {
    position: absolute; left: 0; right: 0; top: 288px; text-align: center;
    font-size: 14px; font-weight: 700; letter-spacing: 4.6px; color: var(--white);
  }
</style>
</head>
<body>
  <section class="card card-front">
    <div class="interior-photo" role="img" aria-label="Faded photo of a bright white salon interior"></div>
    <div class="brand-name-front">Lashvera</div>
    <div class="brand-locale-front">CRESTMOOR HEIGHTS</div>
    <div class="person">
      <div class="person-name">JORDAN VALE</div>
      <div class="person-role">CEO/FOUNDER</div>
    </div>
    <address class="address">4720 N.Alder Crest<br>Ave Crestmoor Heights<br>CA 90099</address>
    <ul class="contact-list">
      <li><svg viewBox="0 0 16 16" aria-hidden="true"><path d="M3.5 1.5l2.5 0 1 3.5-1.7 1.3a9 9 0 0 0 4.4 4.4l1.3-1.7 3.5 1v2.5c0 .8-.7 1.5-1.5 1.5C6.9 14 2 9.1 2 3c0-.8.7-1.5 1.5-1.5z"/></svg>555 014 7091</li>
      <li><svg viewBox="0 0 16 16" aria-hidden="true"><path d="M1 3h14v10H1z M2 4.2v.3l6 4 6-4v-.3z" fill-rule="evenodd"/></svg>news@lashverastudiolounge</li>
      <li><svg viewBox="0 0 16 16" aria-hidden="true"><path d="M8 1a7 7 0 1 0 0 14A7 7 0 0 0 8 1zm0 1.5c.9 0 1.9 1.8 2.2 4.5H5.8C6.1 4.3 7.1 2.5 8 2.5zM2.6 8.5h2.2c.1 1.6.4 3 1 4A5.5 5.5 0 0 1 2.6 8.5zm0-1A5.5 5.5 0 0 1 5.8 3.5c-.6 1-.9 2.4-1 4zm5.4 6c-.9 0-1.9-1.8-2.2-5h4.4c-.3 3.2-1.3 5-2.2 5zm2.2-1c.6-1 .9-2.4 1-4h2.2a5.5 5.5 0 0 1-3.2 4zm1-5c-.1-1.6-.4-3-1-4a5.5 5.5 0 0 1 3.2 4z"/></svg>www.lashverastudio.example</li>
    </ul>
  </section>

  <section class="card card-back">
    <div class="social">
      <span class="social-item"><span class="dot"></span>Circlebook</span>
      <span class="social-item"><span class="dot"></span>Snapgrid</span>
    </div>
    <div class="brand-name-back">Lashvera</div>
    <div class="brand-locale-back">CRESTMOOR HEIGHTS</div>
    <div class="web-back">www.lashverastudio.example</div>
  </section>
</body>
</html>
```